Fee Detective - Website Design

Create website designs for new FeeDetective.com web application.
We are looking for a clean, playful design based on the attached wireframes and the images we have collected on our PinVault board for inspiration : https://app.pinvault-example.net/7QrTb2kZw4Xc81?p=3Hyd9mLe5Rf
Users of the site will want to be able to quickly run a search using the transaction descriptor they want to identify and see any matching merchants. If they don't get a match then we need then to be able to easily provide further details so we can try and find a match for them
Target Market(s)
Anyone with a bank account
Number of Pages Required
5+ page
Requirements
Must have
- Clean yet playful design, incorporating the themes from our pinvault board

```html
<!DOCTYPE html>
<html lang="en">
<head>
<meta charset="utf-8">
<title>Fee Detective – Website Design</title>
<link rel="stylesheet" href="https://fonts.googleapis.com/css2?family=Fredoka:wght@400;500&family=Poppins:wght@400;500&display=swap">
<style>
:root{
  --stage:#000000;
  --tan-deep:#d69b68;
  --tan-mid:#ecc9a6;
  --cream:#fbf1e6;
  --ink:#111111;
  --muted:#4a3a30;
  --field:#f8e8d8;
  --field-border:#c9a182;
  --button:#6b1f14;
  --link:#7a3020;
  --skyline-a:#c98f5e;
  --skyline-b:#e8c7a6;
}
*{box-sizing:border-box;margin:0;padding:0}
html,body{width:1200px;height:2662px;overflow:hidden;background:var(--stage)}
body{position:relative;font-family:"Poppins",sans-serif;color:var(--ink)}
.screen{
  position:absolute;left:139px;width:921px;overflow:hidden;
  background:linear-gradient(100deg,var(--tan-deep) 0%,var(--tan-mid) 45%,var(--cream) 100%);
}
.screen--home{top:130px;height:518px}
.screen--suggest{top:750px;height:518px}
.screen--results{top:1350px;height:561px}
.screen--empty{top:1970px;height:562px}
.mascot{
  position:absolute;left:447px;top:45px;width:26px;height:72px;border-radius:6px;
  background:linear-gradient(180deg,#c7622a 0%,#b8542a 60%,#1f2340 100%);
}
.brand-title{
  position:absolute;left:0;right:0;top:125px;text-align:center;
  font-family:"Fredoka",sans-serif;font-weight:400;font-size:23px;color:var(--ink);
}
.tagline{
  position:absolute;left:200px;right:200px;top:172px;text-align:center;
  font-size:11.5px;line-height:18px;color:var(--ink);
}
.search{
  position:absolute;left:184px;width:555px;top:229px;
  background:var(--field);border:1px solid var(--field-border);border-radius:6px;
}
.search__text{position:absolute;left:14px;top:12px;font-size:9.5px;color:var(--muted);display:flex;align-items:center;gap:7px}
.search__go{position:absolute;right:9px;width:25px;height:25px;border-radius:50%;background:var(--ink);display:flex;align-items:center;justify-content:center}
.search__rule{position:absolute;left:14px;right:41px;top:35px;height:1px;background:#d9c1ad}
.suggestions{position:absolute;left:14px;top:45px;list-style:none;font-size:9.5px}
.suggestions li{display:flex;align-items:center;gap:6px;height:21px}
.help-link{position:absolute;left:0;right:0;top:331px;text-align:center;font-size:10px;color:var(--muted);text-decoration:underline}
.skyline{
  position:absolute;left:50px;right:50px;bottom:0;height:160px;
  background:linear-gradient(180deg,rgba(201,143,94,0) 0%,rgba(201,143,94,.35) 60%,rgba(160,110,75,.45) 100%);
}
.skyline--faint{opacity:.5}
.section-title{position:absolute;left:0;right:0;text-align:center;font-family:"Fredoka",sans-serif;font-size:14px}
.matches{position:absolute;left:184px;width:555px;top:326px;height:111px;background:var(--field);border-radius:6px;overflow:hidden;border:1px solid var(--field-border)}
.matches__head{height:30px;background:var(--ink);color:#fff;font-size:11px;display:flex;align-items:center;padding-left:16px}
.matches__row{display:flex;align-items:center;height:21.5px;font-size:9.5px;padding-left:16px}
.matches__row:first-of-type{margin-top:5px}
.col-name{width:265px}
.col-conf{width:216px;font-size:8px}
.col-more{color:var(--link);font-size:8.5px}
.crowd-note{position:absolute;left:200px;right:200px;text-align:center;font-size:10px;line-height:15px}
.cta{position:absolute;left:387px;width:147px;height:28px;border-radius:14px;background:var(--button);color:#fff;font-size:8px;font-weight:500;display:flex;align-items:center;justify-content:center}
</style>
</head>
<body>

<section class="screen screen--home">
  <div class="mascot" role="img" aria-label="Illustrated detective mascot in trench coat and hat"></div>
  <h1 class="brand-title">Fee Detective</h1>
  <p class="tagline">Helping you identify those odd and sometimes surprising charges on your bank statements and transaction feeds!</p>
  <div class="search" style="height:84px">
    <div class="search__text">
      <svg width="9" height="9" viewBox="0 0 10 10"><circle cx="4" cy="4" r="3" fill="none" stroke="#111" stroke-width="1.6"/><line x1="6.3" y1="6.3" x2="9.3" y2="9.3" stroke="#111" stroke-width="1.6"/></svg>
      Enter your Transcation Descriptor
    </div>
    <span class="search__go" style="top:50px"><svg width="11" height="11" viewBox="0 0 12 12"><path d="M2 10 L10 2 M4 2 H10 V8" fill="none" stroke="#fff" stroke-width="1"/></svg></span>
  </div>
  <a class="help-link">What is a Transaction Descriptor?</a>
  <div class="skyline" role="img" aria-label="Line drawing of a city skyline"></div>
</section>

<section class="screen screen--suggest">
  <div class="mascot" role="img" aria-label="Illustrated detective mascot in trench coat and hat"></div>
  <h1 class="brand-title">Fee Detective</h1>
  <p class="tagline">Helping you identify those odd and sometimes surprising charges on your bank statements and transaction feeds!</p>
  <div class="search" style="height:112px">
    <div class="search__text">GREENL</div>
    <span class="search__go" style="top:6px"><svg width="11" height="11" viewBox="0 0 12 12"><path d="M2 10 L10 2 M4 2 H10 V8" fill="none" stroke="#fff" stroke-width="1"/></svg></span>
    <div class="search__rule"></div>
    <ul class="suggestions">
      <li><svg width="8" height="9" viewBox="0 0 8 10"><path d="M0 0H5L8 3V10H0Z" fill="#111"/></svg>GREENLEAF PTY LTD ST IVES AU</li>
      <li><svg width="8" height="9" viewBox="0 0 8 10"><path d="M0 0H5L8 3V10H0Z" fill="#111"/></svg>GREENLEAF ONLINE SERVICES AU220223</li>
      <li><svg width="8" height="9" viewBox="0 0 8 10"><path d="M0 0H5L8 3V10H0Z" fill="#111"/></svg>GREENWORKS CLOTHING CO SYDNEY</li>
    </ul>
  </div>
  <div class="skyline" role="img" aria-label="Line drawing of a city skyline"></div>
</section>

<section class="screen screen--results">
  <div class="mascot" role="img" aria-label="Illustrated detective mascot in trench coat and hat"></div>
  <h1 class="brand-title">Fee Detective</h1>
  <p class="tagline">Helping you identify those odd and sometimes surprising charges on your bank statements and transaction feeds!</p>
  <div class="search" style="height:58px">
    <div class="search__text">GREENLEAF PTY LTD ST IVES AU</div>
    <span class="search__go" style="top:6px"><svg width="11" height="11" viewBox="0 0 12 12"><path d="M2 10 L10 2 M4 2 H10 V8" fill="none" stroke="#fff" stroke-width="1"/></svg></span>
  </div>
  <div class="skyline skyline--faint" role="img" aria-label="Faded line drawing of a city skyline"></div>
  <h2 class="section-title" style="top:298px">Top Matches</h2>
  <div class="matches">
    <div class="matches__head"><span class="col-name">Merchant Name</span><span>Confidence</span></div>
    <div class="matches__row"><span class="col-name">Greenleaf Pty Ltd</span><span class="col-conf">High</span><span class="col-more">View More</span></div>
    <div class="matches__row"><span class="col-name">Greenleaf Clothing Co</span><span class="col-conf">Low</span><span class="col-more">View More</span></div>
    <div class="matches__row"><span class="col-name">Greenleaf Online Plc</span><span class="col-conf">Low</span><span class="col-more">View More</span></div>
  </div>
  <p class="crowd-note" style="top:458px">Couldn't find a match? Help us Crowd Source more data by clicking the button below and providing a few details so we can help find it and make it available to everyone.</p>
  <a class="cta" style="top:503px">Help improve our results</a>
</section>

<section class="screen screen--empty">
  <div class="mascot" role="img" aria-label="Illustrated detective mascot in trench coat and hat"></div>
  <h1 class="brand-title">Fee Detective</h1>
  <p class="tagline">Helping you identify those odd and sometimes surprising charges on your bank statements and transaction feeds!</p>
  <div class="search" style="height:58px">
    <div class="search__text">GREENLEAF PTY LTD ST IVES AU</div>
    <span class="search__go" style="top:6px"><svg width="11" height="11" viewBox="0 0 12 12"><path d="M2 10 L10 2 M4 2 H10 V8" fill="none" stroke="#fff" stroke-width="1"/></svg></span>
  </div>
  <div class="skyline skyline--faint" style="height:175px" role="img" aria-label="Faded line drawing of a city skyline"></div>
  <h2 class="section-title" style="top:309px;font-size:12px">mmm, we couldn't find a match</h2>
  <p class="crowd-note" style="top:348px">Couldn't find a match? Help us Crowd Source more data by clicking the button below and providing a few details so we can help find it and make it available to everyone.</p>
  <a class="cta" style="top:404px">Help improve our results</a>
</section>

</body>
</html>
```